Brody's Lot Grading & Trenching

I would like to have business cards created for my land clearing company. We have excavators, skid steers, dump trucks, tractor trailer dump trailers, forestry mulchers along with all size tractors for pasture restoration and arena builds.

Target Market(s)

Both commercial and residential clients

Contact Information for Business Card

Name, phone number, email and website

Colors

Designer to choose colors to be used in the design.

```html
<!DOCTYPE html>
<html lang="en">
<head>
<meta charset="utf-8">
<title>Brody's Lot Grading & Trenching — Business Card</title>
<link href="https://fonts.googleapis.com/css2?family=Passion+One:wght@700&family=Poppins:wght@400;600;800&display=swap" rel="stylesheet">
<style>
  :root {
    --stage: #d6d6d6;
    --gold: #f3b11e;
    --ink: #1b1b1b;
    --paper: #ffffff;
    --grey-text: #3a3a3a;
  }
  * { margin: 0; padding: 0; box-sizing: border-box; }
  html, body { width: 1200px; height: 991px; overflow: hidden; }
  body { background: var(--stage); font-family: 'Poppins', sans-serif; position: relative; }

  .card {
    position: absolute; left: 260px; width: 680px; height: 389px;
    border-radius: 28px; overflow: hidden;
    box-shadow: 0 6px 16px rgba(0,0,0,.18);
  }
  .card--front { top: 62px; background: var(--gold); }
  .card--back { top: 530px; background: var(--paper); }

  /* brand lockup */
  .brand { display: flex; align-items: center; gap: 12px; }
  .brand__dot { width: 30px; height: 30px; border-radius: 50%; background: var(--ink); flex: none; }
  .brand__name { font-family: 'Passion One', sans-serif; font-weight: 700; color: var(--ink); line-height: 1; }

  .card--front .brand { position: absolute; top: 58px; left: 0; right: 0; justify-content: center; }
  .card--front .brand__name { font-size: 40px; }

  .services__title {
    position: absolute; top: 152px; left: 0; right: 0; text-align: center;
    font-family: 'Passion One', sans-serif; font-size: 34px; color: var(--paper);
    letter-spacing: 1px; text-shadow: 0 2px 0 rgba(0,0,0,.35);
  }
  .services {
    position: absolute; top: 212px; left: 40px; right: 40px;
    list-style: none; display: flex; flex-wrap: wrap; justify-content: center; gap: 14px 26px;
  }
  .services__item {
    display: flex; align-items: center; gap: 8px;
    font-weight: 800; font-size: 16px; color: var(--paper); letter-spacing: .5px;
    text-transform: uppercase; text-shadow: 0 1.5px 0 rgba(0,0,0,.4);
  }
  .services__item svg { width: 22px; height: 22px; flex: none; }

  /* back */
  .card--back .brand { position: absolute; left: 34px; top: 160px; width: 270px; flex-direction: column; align-items: flex-start; gap: 14px; }
  .card--back .brand__dot { width: 40px; height: 40px; }
  .card--back .brand__name { font-size: 40px; }

  .divider { position: absolute; left: 330px; top: 40px; width: 2px; height: 310px; background: var(--gold); }

  .person { position: absolute; left: 370px; top: 42px; }
  .person__name { font-family: 'Passion One', sans-serif; font-size: 44px; color: var(--ink); line-height: 1; }
  .person__role { font-weight: 600; font-size: 17px; color: var(--gold); letter-spacing: 1px; }

  .contacts { position: absolute; left: 370px; top: 150px; list-style: none; }
  .contacts__item { display: flex; align-items: center; gap: 12px; font-weight: 600; font-size: 16px; color: var(--ink); margin-bottom: 12px; }
  .contacts__icon { width: 28px; height: 28px; border-radius: 50%; background: var(--gold); display: flex; align-items: center; justify-content: center; flex: none; }
  .contacts__icon svg { width: 16px; height: 16px; }

  .company { position: absolute; left: 370px; top: 282px; }
  .company__name { font-weight: 800; font-size: 24px; color: var(--gold); text-transform: uppercase; line-height: 1.1; letter-spacing: .5px; }
  .company__place { font-weight: 600; font-size: 16px; color: var(--ink); margin-top: 6px; }
</style>
</head>
<body>

<section class="card card--front" aria-label="Card front">
  <div class="brand">
    <span class="brand__dot"></span>
    <span class="brand__name">Brody's Lot Grading &amp; Trenching</span>
  </div>
  <h2 class="services__title">SERVICES :</h2>
  <ul class="services">
    <li class="services__item"><svg viewBox="0 0 24 24"><rect x="2" y="5" width="16" height="16" fill="none" stroke="#1b1b1b" stroke-width="2.6"/><path d="M6 12l4 4 11-13" fill="none" stroke="#1b1b1b" stroke-width="3"/></svg>Excavation Services</li>
    <li class="services__item"><svg viewBox="0 0 24 24"><rect x="2" y="5" width="16" height="16" fill="none" stroke="#1b1b1b" stroke-width="2.6"/><path d="M6 12l4 4 11-13" fill="none" stroke="#1b1b1b" stroke-width="3"/></svg>Gardening</li>
    <li class="services__item"><svg viewBox="0 0 24 24"><rect x="2" y="5" width="16" height="16" fill="none" stroke="#1b1b1b" stroke-width="2.6"/><path d="M6 12l4 4 11-13" fill="none" stroke="#1b1b1b" stroke-width="3"/></svg>Land Cleaning</li>
    <li class="services__item"><svg viewBox="0 0 24 24"><rect x="2" y="5" width="16" height="16" fill="none" stroke="#1b1b1b" stroke-width="2.6"/><path d="M6 12l4 4 11-13" fill="none" stroke="#1b1b1b" stroke-width="3"/></svg>Forestry Mulching</li>
    <li class="services__item"><svg viewBox="0 0 24 24"><rect x="2" y="5" width="16" height="16" fill="none" stroke="#1b1b1b" stroke-width="2.6"/><path d="M6 12l4 4 11-13" fill="none" stroke="#1b1b1b" stroke-width="3"/></svg>Pastur Reseeding</li>
    <li class="services__item"><svg viewBox="0 0 24 24"><rect x="2" y="5" width="16" height="16" fill="none" stroke="#1b1b1b" stroke-width="2.6"/><path d="M6 12l4 4 11-13" fill="none" stroke="#1b1b1b" stroke-width="3"/></svg>Build Arenas</li>
    <li class="services__item"><svg viewBox="0 0 24 24"><rect x="2" y="5" width="16" height="16" fill="none" stroke="#1b1b1b" stroke-width="2.6"/><path d="M6 12l4 4 11-13" fill="none" stroke="#1b1b1b" stroke-width="3"/></svg>Resolping</li>
  </ul>
</section>

<section class="card card--back" aria-label="Card back">
  <div class="brand">
    <span class="brand__dot"></span>
    <span class="brand__name">Brody's Lot Grading &amp; Trenching</span>
  </div>
  <div class="divider"></div>
  <div class="person">
    <h1 class="person__name">Dale Harper</h1>
    <p class="person__role">President</p>
  </div>
  <ul class="contacts">
    <li class="contacts__item"><span class="contacts__icon"><svg viewBox="0 0 24 24"><path d="M6 3l4 4-2 3a12 12 0 006 6l3-2 4 4-3 3C10 21 3 14 3 6z" fill="#fff"/></svg></span>(555) 014-2271</li>
    <li class="contacts__item"><span class="contacts__icon"><svg viewBox="0 0 24 24"><rect x="3" y="6" width="18" height="12" fill="none" stroke="#fff" stroke-width="2.2"/><path d="M3 6l9 7 9-7" fill="none" stroke="#fff" stroke-width="2.2"/></svg></span>info@brodyslotgrading.com</li>
    <li class="contacts__item"><span class="contacts__icon"><svg viewBox="0 0 24 24"><circle cx="12" cy="12" r="9" fill="none" stroke="#fff" stroke-width="2"/><path d="M3 12h18M12 3c4 4 4 14 0 18M12 3c-4 4-4 14 0 18" fill="none" stroke="#fff" stroke-width="1.6"/></svg></span>www.brodyslotgrading.com</li>
  </ul>
  <div class="company">
    <p class="company__name">Brody's Lot Grading<br>&amp; Trenching</p>
    <p class="company__place">Cedar Hollow</p>
  </div>
</section>

</body>
</html>
```